Dunmore Roofing

Want a professional looking business card

Industry/Entity Type

Business

Contact Information for Business Card

Paul Dunmore ( Owner) paul@dunmoreroofing-example.com, www.dunmoreroofing-example.com, Adress: 4172 Township road 43 Plantagenet,ON K9X4T2

```html
<!DOCTYPE html>
<html lang="en">
<head>
<meta charset="utf-8">
<title>Dunmore Roofing – Business Card</title>
<link href="https://fonts.googleapis.com/css2?family=Roboto:wght@400;500;700;900&display=swap" rel="stylesheet">
<style>
  :root {
    --backdrop: #e8e5e1;
    --card-white: #f4f4f4;
    --brand-blue: #1b4a8c;
    --text-grey: #4a4a4a;
    --muted-grey: #7a7a7a;
    --rule-grey: #c9c9c9;
    --white: #ffffff;
  }
  * { margin: 0; padding: 0; box-sizing: border-box; }
  html, body {
    width: 1200px; height: 960px; overflow: hidden;
    background: var(--backdrop);
    font-family: "Roboto", Arial, sans-serif;
  }
  .canvas { position: relative; width: 1200px; height: 960px; }

  .card { position: absolute; width: 600px; height: 342px; box-shadow: 0 2px 6px rgba(0,0,0,.18); }

  /* Front */
  .card-front { left: 315px; top: 123px; background: var(--card-white); overflow: hidden; }
  .brand-block {
    position: absolute; left: 15px; width: 320px; top: 182px;
    text-align: center;
  }
  .brand-name {
    display: block; font-weight: 900; font-size: 34px; letter-spacing: 4px;
    padding-left: 4px; line-height: 1; color: var(--brand-blue);
  }
  .brand-tagline {
    display: block; font-weight: 900; font-size: 14px; letter-spacing: 24px;
    margin-top: 5px; padding-left: 24px; line-height: 1; color: var(--muted-grey);
  }
  .divider {
    position: absolute; left: 320px; top: 88px; width: 1px; height: 175px;
    background: linear-gradient(to bottom, transparent, var(--rule-grey) 15%, var(--rule-grey) 85%, transparent);
  }
  .contact-block { position: absolute; left: 346px; top: 95px; color: var(--text-grey); }
  .person-name {
    font-weight: 700; font-size: 19px; letter-spacing: 2.5px; color: var(--brand-blue); line-height: 1;
  }
  .person-role {
    font-size: 11px; letter-spacing: 3px; color: var(--muted-grey); margin-top: 6px; font-weight: 500;
  }
  .address { margin-top: 10px; font-size: 14px; line-height: 19px; }
  .contact-list { list-style: none; margin-top: 9px; font-size: 13.5px; line-height: 19px; }
  .contact-list li { display: flex; align-items: center; gap: 8px; }
  .contact-list svg { width: 12px; height: 12px; fill: var(--brand-blue); flex: none; }
  .front-band { position: absolute; left: 0; bottom: 0; width: 600px; height: 28px; }

  /* Back */
  .card-back {
    left: 312px; top: 482px; background: var(--brand-blue); color: var(--white); text-align: center;
  }
  .back-brand { position: absolute; left: 0; right: 0; top: 133px; }
  .back-name {
    display: block; font-weight: 900; font-size: 38px; letter-spacing: 6px;
    padding-left: 6px; line-height: 1;
  }
  .back-tagline {
    display: block; font-weight: 900; font-size: 15px; letter-spacing: 26px;
    margin-top: 5px; padding-left: 26px; line-height: 1;
  }
  .back-web { display: block; font-size: 14px; letter-spacing: 1.6px; margin-top: 5px; font-weight: 500; }
</style>
</head>
<body>
<main class="canvas">

  <section class="card card-front" aria-label="Business card front">
    <div class="brand-block">
      <span class="brand-name">DUNMORE</span>
      <span class="brand-tagline">ROOFING</span>
    </div>

    <div class="divider"></div>

    <div class="contact-block">
      <h1 class="person-name">PAUL DUNMORE</h1>
      <p class="person-role">OWNER</p>
      <p class="address">4172 Township road 43<br>Fernbrook, ON K9X4T2</p>
      <ul class="contact-list">
        <li>
          <svg viewBox="0 0 24 24" aria-hidden="true"><path d="M6.6 10.8a15.1 15.1 0 0 0 6.6 6.6l2.2-2.2c.3-.3.7-.4 1-.2 1.1.4 2.3.6 3.6.6.6 0 1 .4 1 1V20c0 .6-.4 1-1 1A17 17 0 0 1 3 4c0-.6.4-1 1-1h3.5c.6 0 1 .4 1 1 0 1.3.2 2.5.6 3.6.1.3 0 .7-.2 1z"/></svg>
          613 555 0142
        </li>
        <li>
          <svg viewBox="0 0 24 24" aria-hidden="true"><path d="M2 5h20v14H2z M3.5 6.5 12 13l8.5-6.5" fill="none" stroke="#1b4a8c" stroke-width="2.5"/><path d="M2 5h20l-10 8z"/></svg>
          paul@dunmoreroofing-example.com
        </li>
        <li>
          <svg viewBox="0 0 24 24" aria-hidden="true"><circle cx="12" cy="12" r="10"/><path d="M7 6c2 1 3 3 2 5s1 3 2 5M15 4c-1 2 0 3 2 4s3 3 2 5" fill="none" stroke="#f4f4f4" stroke-width="1.8"/></svg>
          www.dunmoreroofing-example.com
        </li>
      </ul>
    </div>

    <svg class="front-band" viewBox="0 0 600 28" aria-hidden="true">
      <polyline points="0,3 528,3 543,16 558,3 600,3" fill="none" stroke="#9a9a9a" stroke-width="1.2"/>
      <polygon points="0,10 530,10 543,21 556,10 600,10 600,28 0,28" fill="var(--brand-blue)"/>
    </svg>
  </section>

  <section class="card card-back" aria-label="Business card back">
    <div class="back-brand">
      <span class="back-name">DUNMORE</span>
      <span class="back-tagline">ROOFING</span>
      <span class="back-web">www.dunmoreroofing-example.com</span>
    </div>
  </section>

</main>
</body>
</html>
```